Simple and Clean business card design

We would like the design to be simple clean and to incorporate our colors.

We are open to your design and talent, we have the dots in our logo as we think of it as data points and we connect data points for people.

We are open to see the great creative and clean design you bring to the table

Contact Information for Business Card

please include: name, position, email, phone and website

Font styles to use
Sans Serif

Requirements
Must have
• my colors incorporated, simplicity
Nice to have
• lots of white space, simplicity
Should not have
• complexicity/ complex art

```html
<!DOCTYPE html>
<html lang="en">
<head>
<meta charset="utf-8">
<title>Dotwell Business Card</title>
<link href="https://fonts.googleapis.com/css2?family=Lato:wght@400;700&display=swap" rel="stylesheet">
<style>
  :root {
    --stage: #a3a3a3;
    --brand-blue: #4285f4;
    --brand-green: #34a853;
    --brand-yellow: #fbbc05;
    --brand-red: #ea4335;
    --ink: #111111;
    --paper: #ffffff;
    --rule: #777777;
  }
  * { margin: 0; padding: 0; box-sizing: border-box; }
  html, body {
    width: 1200px; height: 1200px; overflow: hidden;
    background: var(--stage);
  }
  .stage { position: relative; width: 1200px; height: 1200px; }
  .card {
    position: absolute; top: 303px; width: 368px; height: 594px;
    box-shadow: 3px 4px 6px rgba(0,0,0,0.45);
    font-family: "Lato", Arial, sans-serif;
  }
  .card--front { left: 200px; background: var(--brand-blue); }
  .card--back { left: 600px; background: var(--paper); }

  .front-fill { position: absolute; inset: 0; background: var(--brand-blue); }

  .wordmark {
    position: absolute; left: 0; right: 0; text-align: center;
    font-weight: 700; font-size: 72px; letter-spacing: 1px; line-height: 1;
  }
  .card--front .wordmark { top: 478px; color: var(--paper); }
  .card--back .wordmark { top: 140px; color: var(--ink); }
  .wordmark-dot {
    position: absolute; width: 22px; height: 22px; border-radius: 50%;
    background: var(--brand-blue); left: 324px; top: 126px;
  }

  .person { position: absolute; top: 382px; left: 0; right: 0; text-align: center; }
  .person-name {
    color: var(--brand-blue); font-weight: 700; font-size: 26px; line-height: 30px;
  }
  .person-role { color: var(--ink); font-size: 17px; line-height: 22px; }

  .icon-row {
    position: absolute; top: 448px; left: 0; right: 0;
    display: flex; justify-content: center; align-items: center; gap: 4px;
  }
  .icon-rule { width: 21px; height: 1px; background: var(--rule); margin: 0 2px; }
  .icon { width: 25px; height: 25px; display: block; }

  .contact {
    position: absolute; top: 479px; left: 0; right: 0; text-align: center;
    color: var(--ink); font-size: 17px; line-height: 25px; letter-spacing: 0.2px;
  }
</style>
</head>
<body>
<main class="stage">
  <section class="card card--front">
    <div class="front-fill" role="img" aria-label="Pattern of faint overlapping outlined circles in blue"></div>
    <div class="wordmark">Dotwell</div>
  </section>

  <section class="card card--back">
    <div class="wordmark">Dotwell</div>
    <span class="wordmark-dot"></span>

    <div class="person">
      <div class="person-name">OWEN MARSH</div>
      <div class="person-role">Founder/ CEO</div>
    </div>

    <div class="icon-row">
      <span class="icon-rule"></span>
      <svg class="icon" viewBox="0 0 24 24" aria-label="Phone">
        <circle cx="12" cy="12" r="12" fill="var(--brand-green)"/>
        <path d="M8.5 6.5l2 2.2-1.2 1.4c.8 1.7 2 2.9 3.6 3.7l1.4-1.2 2.2 2-1.3 1.8c-3.8-.4-7.2-3.8-7.6-7.6z" fill="#fff"/>
      </svg>
      <svg class="icon" viewBox="0 0 24 24" aria-label="Email">
        <circle cx="12" cy="12" r="12" fill="var(--brand-yellow)"/>
        <rect x="6.5" y="8" width="11" height="8" fill="#fff"/>
        <path d="M6.5 8l5.5 4.5L17.5 8" fill="none" stroke="var(--brand-yellow)" stroke-width="1"/>
      </svg>
      <svg class="icon" viewBox="0 0 24 24" aria-label="Website">
        <circle cx="12" cy="12" r="12" fill="var(--brand-red)"/>
        <g fill="none" stroke="#fff" stroke-width="1">
          <circle cx="12" cy="12" r="5.5"/>
          <ellipse cx="12" cy="12" rx="2.4" ry="5.5"/>
          <path d="M6.5 12h11M7.3 9.2h9.4M7.3 14.8h9.4"/>
        </g>
      </svg>
      <span class="icon-rule"></span>
    </div>

    <div class="contact">
      <div>555-204-8817</div>
      <div>owen.marsh@dotwell.one</div>
      <div>www.Dotwell.one</div>
    </div>
  </section>
</main>
</body>
</html>
```